Celvara Health Group Presentation Folder, for Cancer Awareness, VERY COLORFUL AND MODERN

Presentation Folder I know pretty much what i want so it should be very eazy , I have included files from folders I use now rebrand them to my new company they will be fine, no sense re creating the wheel
Full Bleed Size
20.87" x 16.68"
53 x 42.4 cm
6260 x 5004 pixels
Document Trim Size
20.75" x 16.56"
52.7 x 42.1 cm
6225 x 4969 pixels

Low design quality

Industry/Entity Type

Medical

Font styles to use
Serif

Colors

Designer to choose colors to be used in the design.

Requirements
Must have
• really I am not looking for some one to redesign, we like our folder front page and would like to see new word information added., there are two folder front pages to choose from
• So Keep the original front page and redesign the back page and the pockets
• Can Make your Design off of one of the ones I already uploaded
Nice to have
• Keep the same color schemes, Keep the original front page and redesign the back page and the pockets
Should not have
• DO not recreate the front covers, use what I gave you and just rebrand

```html
<!DOCTYPE html>
<html lang="en">
<head>
<meta charset="utf-8">
<title>Celvara Health Group — Presentation Folder</title>
<link rel="stylesheet" href="https://fonts.googleapis.com/css2?family=Raleway:wght@400;600;700;800&family=Noto+Sans:wght@400&display=swap">
<style>
  :root {
    --backdrop: #e6e6e6;
    --paper: #ffffff;
    --green: #9bc266;
    --navy: #17307a;
    --navy-deep: #0f2260;
    --pink: #e9506d;
    --sky: #2f9fd8;
    --frame: #8fd3ee;
    --strip: #d2d2d2;
    --pocket-light: #f4f4f4;
    --trim: #e36a5a;
  }
  * { box-sizing: border-box; margin: 0; padding: 0; }
  html, body { width: 902px; height: 1200px; overflow: hidden; }
  body { background: var(--backdrop); font-family: "Raleway", sans-serif; position: relative; }

  .folder { position: absolute; left: 31px; top: 265px; width: 840px; height: 670px; }
  .folder-shapes { position: absolute; inset: 0; }

  .panel { position: absolute; top: 13px; height: 461px; border: 1px solid var(--frame); }
  .panel-left { left: 45px; width: 361px; }
  .panel-right { left: 433px; width: 362px; text-align: center; }

  .family-photo {
    position: absolute; left: 46px; top: 15px; width: 260px; height: 260px; border-radius: 50%;
    background: radial-gradient(circle at 50% 40%, #f3e6dc 0%, #d9b9a2 45%, #8a7063 75%, #1d2f6f 100%);
  }
  .intro { position: absolute; left: 12px; top: 290px; width: 327px; font-size: 9.4px; line-height: 12.4px; color: #444; text-align: justify; }
  .intro strong { color: var(--pink); font-weight: 700; }
  .motto { position: absolute; left: 12px; top: 379px; width: 327px; text-align: center; font-weight: 700; font-size: 12.6px; line-height: 15.6px; color: var(--navy-deep); }
  .motto .lead { color: var(--pink); display: block; }

  .screen-title { margin-top: 33px; font-size: 20.5px; font-weight: 700; color: var(--pink); letter-spacing: 0.2px; }
  .screen-sub { margin-top: 5px; font-size: 10px; font-weight: 700; color: var(--navy-deep); }
  .screen-note { margin: 11px auto 0; width: 310px; font-size: 8.6px; line-height: 11.8px; color: var(--sky); text-transform: uppercase; }

  .dinner-photo {
    position: absolute; left: 24px; top: 167px; width: 305px; height: 210px; transform: rotate(-4deg);
    background: linear-gradient(160deg, #f1ede6 0%, #cfb8a1 45%, #9a7b62 100%);
    border: 4px solid var(--paper); box-shadow: 2px 4px 10px rgba(0,0,0,0.35);
  }
  .ribbon-mark {
    position: absolute; left: 292px; top: 132px; width: 36px; height: 62px; border-radius: 18px 18px 6px 6px;
    background: linear-gradient(90deg, #6cc3ec 0%, #c88ab8 100%);
  }
  .tagline { position: absolute; left: 12px; top: 421px; display: flex; align-items: center; gap: 10px; font-family: "Noto Sans", sans-serif; font-size: 15px; color: var(--navy-deep); }
  .tagline .dot { width: 32px; height: 32px; border-radius: 50%; background: var(--navy); }
</style>
</head>
<body>
<main class="folder">
  <svg class="folder-shapes" width="840" height="670" viewBox="0 0 840 670" aria-hidden="true">
    <!-- flaps -->
    <rect x="0" y="3" width="32" height="460" fill="var(--green)"/>
    <rect x="808" y="3" width="32" height="460" fill="var(--green)"/>
    <circle cx="0" cy="307" r="14" fill="var(--backdrop)" stroke="var(--trim)" stroke-width="0.8"/>
    <circle cx="840" cy="307" r="14" fill="var(--backdrop)" stroke="var(--trim)" stroke-width="0.8"/>
    <!-- inside spread -->
    <rect x="32" y="0" width="776" height="487" fill="var(--paper)"/>
    <line x1="32" y1="0.5" x2="808" y2="0.5" stroke="var(--trim)" stroke-width="0.8"/>
    <line x1="420" y1="0" x2="420" y2="670" stroke="var(--green)" stroke-width="0.8" stroke-dasharray="3 3"/>
    <line x1="32" y1="487" x2="808" y2="487" stroke="#999" stroke-width="0.6" stroke-dasharray="3 3"/>

    <!-- left pocket -->
    <path d="M33 487 H415 L392 670 H33 Z" fill="var(--paper)" stroke="var(--trim)" stroke-width="0.8"/>
    <path d="M210 670 Q340 640 345 487 H415 L392 670 Z" fill="var(--green)"/>
    <path d="M57 487 H340 Q340 640 180 670 H57 Z" fill="var(--pocket-light)" stroke="#dedede"/>
    <rect x="33" y="487" width="24" height="183" fill="var(--strip)"/>
    <g stroke="var(--trim)" stroke-width="0.9">
      <line x1="150" y1="562" x2="175" y2="538"/>
      <line x1="272" y1="538" x2="297" y2="562"/>
      <line x1="150" y1="598" x2="175" y2="622"/>
      <line x1="272" y1="622" x2="297" y2="598"/>
    </g>
    <g transform="rotate(180 215 515)" text-anchor="middle" font-family="Raleway, sans-serif">
      <text x="215" y="512" font-size="13.5" fill="var(--pink)" letter-spacing="0.5">CELVARA HEALTH GROUP</text>
      <text x="215" y="527" font-size="9" fill="var(--pink)">a division of Meridian Medical Sales LLC</text>
    </g>

    <!-- right pocket -->
    <path d="M423 487 H808 V670 H462 Q452 670 450 660 Z" fill="var(--green)" stroke="var(--trim)" stroke-width="0.8"/>
    <path d="M520 487 H781 V670 H640 Q520 640 520 487 Z" fill="var(--paper)" stroke="#dedede"/>
    <rect x="781" y="487" width="27" height="183" fill="var(--strip)"/>
    <rect x="442" y="502" width="331" height="155" fill="none" stroke="var(--frame)" stroke-width="0.9"/>
    <g transform="rotate(180 655 560)">
      <circle cx="590" cy="560" r="26" fill="var(--navy)"/>
      <text x="628" y="566" font-family="Raleway, sans-serif" font-weight="800" font-size="19" fill="var(--navy-deep)">CELVARA HEALTH GROUP</text>
    </g>
  </svg>

  <section class="panel panel-left">
    <div class="family-photo" role="img" aria-label="Photo of a smiling multi-generation family"></div>
    <p class="intro"><strong>Hereditary cancer screening</strong> provides vital information to help people with a strong personal or family history of cancer understand their own risk of developing the disease. With this information, they can take steps to Potentially Prevent Cancer, Delay the Onset of Cancer or Catch it at an Earlier stage when outcomes and survival rates are Better.</p>
    <p class="motto"><span class="lead">Don't be Afraid of the Answer:</span>Knowledge is Power and Power Eradicates Fear. When You are Fearless, You Will Make all the Right Choices!</p>
  </section>

  <section class="panel panel-right">
    <h1 class="screen-title">HEREDITARY CANCER SCREENING</h1>
    <p class="screen-sub">DOCTORS ARE THE GATEKEEPERS TO GENETIC TESTING.</p>
    <p class="screen-note">We have an obligation to help patients understand genetic risk and how testing can guide heath care decisions.</p>
    <div class="dinner-photo" role="img" aria-label="Photo of a family sharing a meal at an outdoor table"></div>
    <div class="ribbon-mark" role="img" aria-label="Blue and pink awareness ribbon"></div>
    <p class="tagline"><span class="dot"></span>The test you order FOR your patients</p>
  </section>
</main>
</body>
</html>
```